business card deign

Logo needs the following on it.
1. attached logo
2. Tagline - "When The Ice Holds Out And The Music Plays On...That's Us!"
3. Name- Dalton Pikes, Founder and CPO
4. Address - 412 E. Carver Avenue, Ste 2207, Brenton, GA. 33917
5. Phone - 555.318.4726

```html
<!DOCTYPE html>
<html lang="en">
<head>
<meta charset="utf-8">
<title>Hopwell Business Card</title>
<link rel="stylesheet" href="https://fonts.googleapis.com/css2?family=Lato:wght@300;400;700&family=Marcellus&display=swap">
<style>
  :root {
    --page-bg: #ecebe8;
    --card-white: #ffffff;
    --card-black: #050505;
    --ink-dark: #111111;
    --ink-light: #f4f4f4;
    --ink-soft: #cfcfcf;
    --rule-light: #d8d8d8;
    --rule-dark: #6a6a6a;
    --ghost: #1c1c1c;
  }
  * { margin: 0; padding: 0; box-sizing: border-box; }
  html, body {
    width: 1200px; height: 900px; overflow: hidden;
    background: var(--page-bg);
    font-family: "Lato", sans-serif;
  }
  .card {
    position: absolute; left: 250px;
    width: 700px; height: 400px;
    border-radius: 34px;
    overflow: hidden;
    box-shadow: 0 10px 28px rgba(0,0,0,0.18);
  }
  .card--front { top: 36px; background: linear-gradient(160deg, var(--card-white) 55%, #eeeeee); }
  .card--back { top: 466px; background: var(--card-black); }

  .brand {
    font-family: "Lato", sans-serif;
    font-weight: 700;
    letter-spacing: 0.42em;
    text-transform: uppercase;
    display: flex; align-items: center; gap: 18px;
  }
  .brand-dot { width: 22px; height: 22px; border-radius: 50%; }

  .card--front .brand {
    position: absolute; top: 140px; left: 0; right: 0;
    justify-content: center;
    font-size: 40px; color: var(--ink-dark);
  }
  .card--front .brand-dot { background: var(--ink-dark); }
  .front-rule {
    position: absolute; top: 232px; left: 120px; right: 120px;
    height: 1px; background: var(--rule-light);
  }
  .tagline {
    position: absolute; top: 250px; left: 0; right: 0;
    text-align: center;
    font-family: "Marcellus", serif;
    font-size: 20px; color: var(--ink-dark);
  }

  .ghost-mark {
    position: absolute; left: 360px; top: -30px;
    width: 300px; height: 300px; border-radius: 50%;
    background: var(--ghost);
  }
  .card--back .brand {
    position: absolute; left: 60px; top: 150px;
    font-size: 44px; color: var(--ink-light);
  }
  .card--back .brand-dot { background: var(--ink-light); }

  .contact-block {
    position: absolute; right: 40px; bottom: 52px;
    display: flex; align-items: stretch; gap: 18px;
    color: var(--ink-soft);
  }
  .person { text-align: right; display: flex; flex-direction: column; justify-content: flex-end; }
  .person-title { font-weight: 300; font-size: 19px; }
  .person-name { font-weight: 700; font-size: 21px; color: var(--ink-light); text-transform: uppercase; }
  .divider { width: 1px; background: var(--rule-dark); }
  .details { font-size: 18px; font-weight: 300; line-height: 1.45; }
  .detail-row { display: flex; gap: 10px; align-items: flex-start; }
  .detail-row svg { width: 16px; height: 16px; margin-top: 5px; flex: none; }
</style>
</head>
<body>
  <section class="card card--front">
    <div class="brand"><span class="brand-dot"></span>Hopwell</div>
    <div class="front-rule"></div>
    <p class="tagline">When The Ice Holds Out And The Music Plays On…That's Us!</p>
  </section>

  <section class="card card--back">
    <div class="ghost-mark"></div>
    <div class="brand"><span class="brand-dot"></span>Hopwell</div>
    <div class="contact-block">
      <div class="person">
        <span class="person-title">Founder and CPO</span>
        <span class="person-name">Dalton Pikes</span>
      </div>
      <div class="divider"></div>
      <div class="details">
        <div class="detail-row">
          <svg viewBox="0 0 24 24" fill="#cfcfcf"><path d="M6.6 10.8a15.1 15.1 0 0 0 6.6 6.6l2.2-2.2c.3-.3.7-.4 1-.2 1.1.4 2.3.6 3.6.6.6 0 1 .4 1 1V20c0 .6-.4 1-1 1A17 17 0 0 1 3 4c0-.6.4-1 1-1h3.5c.6 0 1 .4 1 1 0 1.3.2 2.5.6 3.6.1.3 0 .7-.2 1z"/></svg>
          <span>555.318.4726</span>
        </div>
        <div class="detail-row">
          <svg viewBox="0 0 24 24" fill="#cfcfcf"><path d="M12 2a7 7 0 0 0-7 7c0 5.2 7 13 7 13s7-7.8 7-13a7 7 0 0 0-7-7zm0 9.5A2.5 2.5 0 1 1 12 6.5a2.5 2.5 0 0 1 0 5z"/></svg>
          <span>412 E. Carver Avenue, Ste 2207<br>Brenton, GA. 33917</span>
        </div>
      </div>
    </div>
  </section>
</body>
</html>
```